Motor Oil Lubricant Package Labels

We are looking for a logo and label that we can put on our motor oil bottle 1 liter and 5 liter. The name of our motor oil is Corvana. We want to design our flagship logo for CORVANA MOTOR OILS and as well as the label that will go on the bottle. We have some drafts that we have come up with attached and would like to see more options. The concept of a timeless motor oil and the endless loop of lubricating oils incorporated in the design. We will have full synthetic motor oil, a synthetic blend motor, ATF III transmission fluid, KRL-VI transmission fluid. hydraulic oils etc. Examples will be attached
Target Market(s)
Automotive Lubricants and Chemicals
Industry/Entity Type
Automotive
Logo Text
Corvana Lubricants
Font styles to use
Other font styles liked:
- Let designer choose
Requirements
Must have
- The Corvana sign incorporated in a very cool way to our name. Our brand needs to stick out
Nice to have
- Automotive lubricant related and colors red, white, and blue incorporated in the design
Should not have
- Images of individuals and or topics not related to automotive lubricants.

```html
<!DOCTYPE html>
<html lang="en">
<head>
<meta charset="utf-8">
<title>Corvana Motor Oil Labels</title>
<link rel="stylesheet" href="https://fonts.googleapis.com/css2?family=Roboto+Condensed:wght@400;700;900&family=Roboto:wght@500&display=swap">
<style>
  :root {
    --page: #e9e9ea;
    --steel-light: #f2f2f2;
    --steel-mid: #b9b9bb;
    --steel-dark: #7c7c7e;
    --oil-red: #ec1c24;
    --blue-bright: #2f55ad;
    --blue-deep: #1f3f95;
    --ink: #1c1c1c;
    --white: #ffffff;
    --gold: #d6a53a;
    --gold-light: #f6dc8c;
  }
  * { margin: 0; padding: 0; box-sizing: border-box; }
  html, body { width: 1200px; height: 935px; overflow: hidden; }
  body {
    background: radial-gradient(ellipse at center, #f4f4f5 0%, var(--page) 70%, #dcdcde 100%);
    font-family: "Roboto Condensed", sans-serif;
    position: relative;
  }
  .label {
    position: absolute;
    top: 117px;
    width: 433px;
    height: 701px;
    border-radius: 26px;
    overflow: hidden;
    box-shadow: 0 0 0 1px #c8c8ca, 0 3px 8px rgba(0,0,0,.12);
    background:
      conic-gradient(from 200deg at 62% 30%, var(--steel-mid), var(--steel-light) 12%, var(--steel-dark) 28%, var(--steel-mid) 42%, var(--steel-light) 55%, var(--steel-dark) 72%, var(--steel-light) 86%, var(--steel-mid));
  }
  .label--front { left: 141px; }
  .label--back { left: 625px; }
  .label__shapes { position: absolute; inset: 0; }
  .brand {
    position: absolute;
    font-weight: 900;
    font-size: 64px;
    color: var(--ink);
    letter-spacing: 0.5px;
    line-height: 1;
    display: flex;
    align-items: center;
    gap: 10px;
    white-space: nowrap;
  }
  .brand__dot {
    width: 20px; height: 20px; border-radius: 50%;
    background: var(--oil-red);
  }
  .label--front .brand { left: 78px; top: 160px; }
  .label--back .brand { left: 112px; top: 128px; font-size: 56px; }

  .grade {
    position: absolute;
    color: var(--white);
    white-space: nowrap;
    display: flex;
    flex-direction: column;
    align-items: flex-start;
    transform: translate(-50%, -50%) rotate(-90deg);
  }
  .label--front .grade { left: 331px; top: 475px; }
  .label--back .grade { left: 359px; top: 456px; transform: translate(-50%, -50%) rotate(-90deg) scale(0.9); }
  .grade__type {
    font-weight: 700; font-size: 20px; letter-spacing: 2.5px;
    line-height: 1; padding-left: 44px; margin-bottom: 4px;
  }
  .grade__row { display: flex; align-items: flex-end; gap: 5px; }
  .grade__sae { font-weight: 900; font-size: 30px; line-height: .8; letter-spacing: 1px; }
  .grade__visc { font-weight: 900; font-size: 78px; line-height: .76; letter-spacing: 3px; }
  .grade__spec {
    display: flex; flex-direction: column;
    font-weight: 900; font-size: 24px; line-height: .86; letter-spacing: 1px;
  }

  .volume {
    position: absolute; left: 42px; top: 652px;
    font-weight: 700; font-size: 22px; color: #262626; white-space: nowrap;
  }
  .origin {
    position: absolute; left: 261px; top: 654px;
    font-weight: 700; font-size: 18px; color: var(--white); white-space: nowrap;
  }
  .seal {
    position: absolute; left: 36px; top: 333px;
    width: 120px; height: 120px; border-radius: 50%;
    background: radial-gradient(circle at 35% 30%, var(--gold-light), var(--gold) 55%, #a97a1d);
    display: flex; align-items: center; justify-content: center;
  }
  .seal__inner {
    width: 86px; height: 86px; border-radius: 50%;
    background: var(--white);
    box-shadow: 0 0 0 3px #b8882a;
    display: flex; align-items: center; justify-content: center; text-align: center;
    font-weight: 700; font-size: 13px; line-height: 1.2; color: var(--ink);
  }
  .made-in {
    position: absolute; left: 47px; top: 547px; width: 93px;
  }
  .made-in__flag {
    display: block; width: 93px; height: 48px;
    background: linear-gradient(to right, #2b3a7c 0 42%, transparent 42%),
                repeating-linear-gradient(to bottom, #c9252c 0 4px, #ffffff 4px 8px);
    background-size: 100% 52%, 100% 100%;
    background-repeat: no-repeat;
  }
  .made-in__text {
    display: block; background: var(--white); text-align: center;
    font-family: "Roboto", sans-serif; font-weight: 500; font-size: 12px;
    letter-spacing: 1px; padding: 1px 0 2px; color: var(--ink); white-space: nowrap;
  }
</style>
</head>
<body>

<section class="label label--front">
  <svg class="label__shapes" viewBox="0 0 433 701" aria-hidden="true">
    <defs>
      <linearGradient id="rim-front" x1="0" y1="0" x2="1" y2="0">
        <stop offset="0" stop-color="#9d9d9f"/><stop offset=".5" stop-color="#ffffff"/><stop offset="1" stop-color="#a8a8aa"/>
      </linearGradient>
    </defs>
    <path d="M0,0 H243 C150,45 45,140 0,250 Z" fill="var(--blue-deep)"/>
    <path d="M0,0 H205 C125,45 35,130 0,215 Z" fill="var(--blue-bright)"/>
    <path d="M433,165 C285,215 175,400 172,701 H433 Z" fill="url(#rim-front)"/>
    <path d="M433,183 C302,232 202,405 199,701 H433 Z" fill="var(--oil-red)"/>
  </svg>
  <div class="brand"><span class="brand__dot"></span>Corvana</div>
  <div class="seal"><div class="seal__inner">FOR<br>GASOLINE<br>ENGIENS</div></div>
  <div class="grade">
    <span class="grade__type">SYNTHETIC BLEND</span>
    <div class="grade__row">
      <span class="grade__sae">SAE</span>
      <span class="grade__visc">5W-30</span>
      <span class="grade__spec"><span>API</span><span>SN</span></span>
    </div>
  </div>
  <span class="volume">32oz 1946 mU</span>
  <span class="origin">Made In USA</span>
</section>

<section class="label label--back">
  <svg class="label__shapes" viewBox="0 0 433 701" aria-hidden="true">
    <defs>
      <linearGradient id="rim-back" x1="0" y1="0" x2="1" y2="0">
        <stop offset="0" stop-color="#9d9d9f"/><stop offset=".5" stop-color="#ffffff"/><stop offset="1" stop-color="#a8a8aa"/>
      </linearGradient>
    </defs>
    <path d="M0,0 H243 C150,45 45,140 0,250 Z" fill="var(--blue-deep)"/>
    <path d="M0,0 H205 C125,45 35,130 0,215 Z" fill="var(--blue-bright)"/>
    <path d="M433,165 C285,215 175,400 172,701 H433 Z" fill="url(#rim-back)"/>
    <path d="M433,183 C302,232 202,405 199,701 H433 Z" fill="var(--oil-red)"/>
  </svg>
  <div class="brand"><span class="brand__dot"></span>Corvana</div>
  <div class="made-in">
    <span class="made-in__flag" role="img" aria-label="United States flag"></span>
    <span class="made-in__text">MADE IN USA</span>
  </div>
  <div class="grade">
    <span class="grade__type">SYNTHETIC BLEND</span>
    <div class="grade__row">
      <span class="grade__sae">SAE</span>
      <span class="grade__visc">5W-30</span>
      <span class="grade__spec"><span>API</span><span>SN</span></span>
    </div>
  </div>
</section>

</body>
</html>
```